Website Design for Bright Path Learning

The business is called Bright Path Learning - a Drug & Alcohol Education program for Sydney school kids. I wish to create a simple online business card which covers who we are, the programs we offer and why they should choose us. I would like the business page to be very colourful and school-friendly, but with the seriousness of alcohol and drug use. I have attached some pictures and logos for the business. The programs are called 'hold firm' for high school, and 'grow wise' for primary school. The logo is black & white. There is also a photo of the manager with some kids.

```html
<!DOCTYPE html>
<html lang="en">
<head>
<meta charset="utf-8">
<title>Bright Path Learning – Mobile Home</title>
<link href="https://fonts.googleapis.com/css2?family=Arvo:wght@400;700&family=Encode+Sans+Condensed:wght@400&display=swap" rel="stylesheet">
<style>
  :root{
    --stage:#000000;
    --page:#ffffff;
    --ink:#231f20;
    --aqua:#2ecbd6;
    --aqua-deep:#1ab5bf;
    --social:#e5dfd3;
    --on-dark:#ffffff;
  }
  *{margin:0;padding:0;box-sizing:border-box}
  html,body{width:1200px;height:1000px;overflow:hidden;background:var(--stage)}
  body{position:relative;font-family:"Arvo",Georgia,serif;color:var(--ink)}

  .side-note{position:absolute;top:90px;width:220px;text-align:center;color:var(--on-dark);font-size:16px;line-height:22px}
  .side-note h2{font-size:16px;font-weight:700;margin-bottom:20px}
  .side-note--left{left:74px}
  .side-note--right{left:915px}

  .mobile-page{position:absolute;left:366px;top:0;width:470px;height:1000px;background:var(--page)}

  .site-header{position:absolute;top:0;left:0;width:100%;text-align:center}
  .brand-name{position:absolute;top:52px;left:0;width:100%;font-size:34px;font-weight:700;color:var(--ink);letter-spacing:.5px}
  .social-links{position:absolute;top:136px;left:201px;display:flex;gap:8px}
  .social-icon{width:30px;height:30px;border-radius:50%;background:var(--social);display:flex;align-items:center;justify-content:center}
  .social-icon svg{width:16px;height:16px;display:block}
  .contact{position:absolute;left:0;width:100%;font-family:"Encode Sans Condensed","Arial Narrow",sans-serif;color:var(--ink)}
  .contact--phone{top:166px;font-size:31px}
  .contact--email{top:202px;font-size:26px}

  .menu-bar{position:absolute;top:260px;left:0;width:468px;height:40px;background:var(--aqua);text-align:center;font-size:17px;line-height:40px;color:var(--ink)}

  .program-grid{position:absolute;top:344px;left:1px;width:468px;height:449px;background:var(--aqua)}
  .tile{position:absolute;width:200px;text-align:center}
  .tile-ring{width:145px;height:145px;border-radius:50%;background:var(--aqua-deep);margin:0 auto;display:flex;align-items:center;justify-content:center}
  .tile-image{width:124px;height:124px;border-radius:50%}
  .tile-label{margin-top:10px;height:18px;border-radius:3px;background:var(--aqua-deep);color:var(--on-dark);font-size:13px;line-height:18px}
  .tile--about{left:18px;top:20px}
  .tile--grow{left:251px;top:20px}
  .tile--hold{left:17px;top:226px}
  .tile--why{left:250px;top:226px}
  .img-manager{background:linear-gradient(160deg,#c9c4bd,#3a3a3f 70%)}
  .img-grow{background:linear-gradient(135deg,#ffffff,#dbe86a 60%,#7ec6d4)}
  .img-hold{background:linear-gradient(135deg,#ffffff,#e8f3e8 60%,#5db34a)}
  .img-family{background:linear-gradient(160deg,#b9c0c6,#5f8fb8 60%,#6a5a4e)}

  .welcome{position:absolute;top:820px;left:0;width:100%;text-align:center;font-size:25px;font-weight:400}
  .intro{position:absolute;top:891px;left:4px;width:462px;text-align:center;font-size:12.5px;line-height:17px;letter-spacing:-.2px}
</style>
</head>
<body>
  <aside class="side-note side-note--left">
    <h2>Mobile Version</h2>
    <p>These black parts would not be visible on the actual site.</p>
  </aside>
  <aside class="side-note side-note--right">
    <h2>Mobile Version</h2>
    <p>These black parts would not be visible on the actual site.</p>
  </aside>

  <main class="mobile-page">
    <header class="site-header">
      <div class="brand-name">Bright Path Learning</div>
      <div class="social-links" aria-label="Social links">
        <span class="social-icon" aria-label="Share">
          <svg viewBox="0 0 16 16" aria-hidden="true">
            <g fill="#ffffff"><circle cx="12" cy="3.5" r="2.2"/><circle cx="4" cy="8" r="2.2"/><circle cx="12" cy="12.5" r="2.2"/></g>
            <path d="M12 3.5 4 8l8 4.5" fill="none" stroke="#ffffff" stroke-width="1.4"/>
          </svg>
        </span>
        <span class="social-icon" aria-label="Message">
          <svg viewBox="0 0 16 16" aria-hidden="true">
            <path d="M2 3h12v8H7l-3.5 3v-3H2z" fill="#ffffff"/>
          </svg>
        </span>
      </div>
      <div class="contact contact--phone">02 5550 1234</div>
      <div class="contact contact--email">info@brightpath.example</div>
    </header>

    <nav class="menu-bar">Menu</nav>

    <section class="program-grid">
      <div class="tile tile--about">
        <div class="tile-ring"><div class="tile-image img-manager" role="img" aria-label="Photo of the program manager"></div></div>
        <div class="tile-label">About us</div>
      </div>
      <div class="tile tile--grow">
        <div class="tile-ring"><div class="tile-image img-grow" role="img" aria-label="Grow Wise program artwork"></div></div>
        <div class="tile-label">Grow Wise Program</div>
      </div>
      <div class="tile tile--hold">
        <div class="tile-ring"><div class="tile-image img-hold" role="img" aria-label="Hold Firm program artwork"></div></div>
        <div class="tile-label">Hold Firm Program</div>
      </div>
      <div class="tile tile--why">
        <div class="tile-ring"><div class="tile-image img-family" role="img" aria-label="Photo of the manager with school kids"></div></div>
        <div class="tile-label">Why choose us</div>
      </div>
    </section>

    <h1 class="welcome">Welcome to Bright Path Learning</h1>
    <p class="intro">Lorem ipsum dolor sit amet, consectetur adipiscing elit. Pellentesque sit amet urna lacus. Nam ipsum felis, condimentum molestie consectetur ac; blandit at felis. Nulla facilisi. Sed id sapien ac massa cursus pretium et id sapien. Ut varius eros vitae turpis porttitor iaculis. Sed eget lacus eu elit rutrum eleifend sed lacinia nulla. Maecenas eu ligula a nulla placerat accumsan eget ac nunc.</p>
  </main>
</body>
</html>
```